Awesome Digital Ad Design – Vexora Adloop

I am going to be setting up a Vexora Adloop ad campaign I need creatives for.

Several sizes are needed in the end, however, please submit your design concept in the following 2 sizes to start:
Medium rectangle: 300X250
Leaderboard: 728X90

Original artwork/design files and images used expected upon payment and as part of the final delivery.

Ads should match our company brand and the information on this webpage: http://www.harbelstandwork.com/real-estate-marketing/
SEE MORE INSTRUCTIONS IN ATTACHED WORD DOC

Target Market(s)

Business-To-Business Audience –Real Estate Company Executives (Presidents/VPs/Owners/CEOs/Sales Managers).

Industry/Entity Type

Real Estate

Font styles to use
Sans Serif

Requirements
Must have
• Copy should be minimal words, billboard like. Please use real photos/images that would appeal to real estate high-level decision-maker executives.
Should not have
• No cartoons or graphics

```html
<!DOCTYPE html>
<html lang="en">
<head>
<meta charset="utf-8">
<title>Harbel Standwork – Display Ads</title>
<link rel="stylesheet" href="https://fonts.googleapis.com/css2?family=Oswald:wght@500;600&family=Questrial&display=swap">
<style>
  :root {
    --stage: #2b2b2b;
    --slate: #4f6d86;
    --maroon: #6a2536;
    --orange: #ea6a2a;
    --orange-dark: #c9521b;
    --white: #ffffff;
    --sky-top: #eef1f4;
    --sky-low: #c9d2da;
    --water: #9aa8b4;
    --ink: #333c44;
  }
  * { box-sizing: border-box; margin: 0; padding: 0; }
  html, body { width: 1200px; height: 1200px; overflow: hidden; }
  body { background: var(--stage); position: relative; font-family: "Oswald", sans-serif; }

  .ad { position: absolute; overflow: hidden; }

  .city-backdrop {
    position: absolute; inset: 0;
    background: linear-gradient(180deg, var(--sky-top) 0%, #dfe5ea 40%, var(--sky-low) 75%, var(--water) 100%);
  }
  .agent-photo {
    position: absolute;
    background: linear-gradient(160deg, #8a5a45 0%, #5a3c36 45%, #3d2b2c 100%);
  }

  .brand-name {
    font-family: "Questrial", sans-serif;
    color: var(--ink);
    font-weight: 400;
    line-height: 1.15;
  }
  .brand-dot { border-radius: 50%; background: var(--maroon); }

  .headline {
    position: absolute; line-height: 1; font-weight: 600;
    text-transform: uppercase; white-space: nowrap;
    text-shadow: 0 0 3px rgba(255,255,255,.9), 1px 1px 0 rgba(255,255,255,.7);
  }
  .slate { color: var(--slate); }
  .maroon { color: var(--maroon); }

  .cta {
    position: absolute; display: flex; align-items: center;
    background: linear-gradient(180deg, #f48a45 0%, var(--orange) 50%, var(--orange-dark) 100%);
    border: 2px solid #f7a877; border-radius: 10px;
    color: var(--white); font-weight: 500; white-space: nowrap;
    box-shadow: 0 2px 4px rgba(0,0,0,.25);
  }

  /* Medium rectangle */
  .ad-rectangle { left: 207px; top: 98px; width: 786px; height: 654px; }
  .ad-rectangle .agent-photo { left: 0; top: 14px; width: 410px; height: 536px; border-radius: 160px 160px 0 0; }
  .ad-rectangle .brand-block {
    position: absolute; left: 330px; top: 2px; width: 134px; height: 130px;
    background: var(--white); display: flex; flex-direction: column; align-items: center; justify-content: center; gap: 8px;
  }
  .ad-rectangle .brand-name { font-size: 16px; text-align: center; }
  .ad-rectangle .brand-dot { width: 14px; height: 14px; }
  .rect-divider { position: absolute; left: 390px; top: 276px; width: 372px; height: 2px; background: rgba(255,255,255,.85); }
  .ad-rectangle .cta { left: 63px; top: 552px; width: 655px; height: 78px; font-size: 44px; padding: 0 18px; gap: 18px; }
  .ad-rectangle .cta .cta-label { flex: 1; }

  /* Leaderboard */
  .ad-leaderboard { left: 56px; top: 915px; width: 1089px; height: 134px; }
  .leader-panel { position: absolute; left: 0; top: 0; width: 190px; height: 100%; }
  .ad-leaderboard .brand-block { position: absolute; left: 18px; top: 48px; display: flex; align-items: center; gap: 6px; }
  .ad-leaderboard .brand-name { font-size: 13px; }
  .ad-leaderboard .brand-dot { width: 9px; height: 9px; }
  .leader-divider { position: absolute; left: 421px; top: 0; width: 3px; height: 100%; background: rgba(255,255,255,.9); }
  .ad-leaderboard .agent-photo { left: 946px; top: 0; width: 143px; height: 134px; border-radius: 60px 0 0 0; }
  .ad-leaderboard .cta { left: 762px; top: 56px; width: 184px; height: 34px; font-size: 20px; padding: 0 6px; gap: 6px; border-radius: 5px; }
</style>
</head>
<body>

<section class="ad ad-rectangle" aria-label="Medium rectangle ad">
  <div class="city-backdrop" role="img" aria-label="Photo of a waterfront city skyline with glass office towers"></div>
  <div class="agent-photo" role="img" aria-label="Photo of a smiling real estate agent holding a sold sign"></div>

  <div class="brand-block">
    <span class="brand-dot"></span>
    <span class="brand-name">Harbel<br>Standwork</span>
  </div>

  <div class="headline slate" style="left:410px; top:162px; font-size:44px;">Client Follow-Up</div>
  <div class="headline maroon" style="left:392px; top:200px; font-size:64px;">Made Simple</div>
  <div class="rect-divider"></div>
  <div class="headline slate" style="left:492px; top:292px; font-size:44px;">Virtually</div>
  <div class="headline slate" style="left:486px; top:334px; font-size:44px;">No Cost To</div>
  <div class="headline maroon" style="left:534px; top:376px; font-size:60px;">Your</div>
  <div class="headline maroon" style="left:503px; top:430px; font-size:60px;">Company!</div>

  <div class="cta">
    <svg width="48" height="48" viewBox="0 0 48 48" aria-hidden="true">
      <path d="M12 8c2-2 5-1 6 1l3 6c1 2 0 3-1 4l-2 2c2 4 5 7 9 9l2-2c1-1 2-2 4-1l6 3c2 1 3 4 1 6l-3 3c-3 3-10 1-17-6S9 14 12 8z" fill="#fff"/>
      <path d="M27 9a13 13 0 0 1 12 12M27 15a7 7 0 0 1 6 6" stroke="#fff" stroke-width="2.5" fill="none" stroke-linecap="round"/>
    </svg>
    <span class="cta-label">CALL TOACTION: LEARN MORE</span>
    <svg width="54" height="54" viewBox="0 0 54 54" aria-hidden="true">
      <circle cx="27" cy="27" r="24" fill="#fff"/>
      <path d="M15 22h13v-8l13 13-13 13v-8H15z" fill="var(--orange)"/>
    </svg>
  </div>
</section>

<section class="ad ad-leaderboard" aria-label="Leaderboard ad">
  <div class="city-backdrop" role="img" aria-label="Photo of a waterfront city skyline with glass office towers"></div>
  <svg class="leader-panel" viewBox="0 0 190 134" preserveAspectRatio="none" aria-hidden="true">
    <path d="M0 0H158C142 30 132 80 128 134H0z" fill="#fff"/>
    <path d="M158 0C142 30 132 80 128 134" stroke="var(--slate)" stroke-width="3" fill="none"/>
  </svg>
  <div class="brand-block">
    <span class="brand-dot"></span>
    <span class="brand-name">Harbel Standwork</span>
  </div>

  <div class="headline slate" style="left:160px; top:25px; font-size:30px;">Client Follow-Up</div>
  <div class="headline slate" style="left:160px; top:58px; font-size:46px;">Made Simple</div>
  <div class="leader-divider"></div>
  <div class="headline maroon" style="left:446px; top:30px; font-size:30px;">Virtually No Cost To</div>
  <div class="headline maroon" style="left:446px; top:58px; font-size:46px;">Your Company!</div>

  <div class="cta">
    <svg width="22" height="22" viewBox="0 0 48 48" aria-hidden="true">
      <path d="M12 8c2-2 5-1 6 1l3 6c1 2 0 3-1 4l-2 2c2 4 5 7 9 9l2-2c1-1 2-2 4-1l6 3c2 1 3 4 1 6l-3 3c-3 3-10 1-17-6S9 14 12 8z" fill="#fff"/>
      <path d="M27 9a13 13 0 0 1 12 12M27 15a7 7 0 0 1 6 6" stroke="#fff" stroke-width="3" fill="none" stroke-linecap="round"/>
    </svg>
    <span class="cta-label">CALL TO ACTION</span>
    <svg width="24" height="24" viewBox="0 0 54 54" aria-hidden="true">
      <circle cx="27" cy="27" r="24" fill="#fff"/>
      <path d="M15 22h13v-8l13 13-13 13v-8H15z" fill="var(--orange)"/>
    </svg>
  </div>

  <div class="agent-photo" role="img" aria-label="Photo of a smiling real estate agent holding a sold sign in front of a house"></div>
</section>

</body>
</html>
```